Boutique custom software development company needs new business card

Our nearly 20 year old custom software development company would like to better include the fact that we are now providing Bitcoin services. These new services are B2B include education (how to acquire and securely hold Bitcoin) and integrating Bitcoin payments into existing ecommerce sites or other existing systems. Please keep the card clean and simple. Attached is our current design and some other files. vextorial.com

Target Market(s)

businesses owners interested in long term relationship

Industry/Entity Type

Custom software development and Bitcoin

Contact Information for Business Card

Dale Parker, dale@vextorial.com, vextorial.com, (888) 555-VXTRL

Font styles to use
Other font styles liked:
• monospace

Requirements
Must have
• double-sided
Nice to have
• clean and simple
Should not have
• physical address

```html
<!DOCTYPE html>
<html lang="en">
<head>
<meta charset="utf-8">
<title>Vextorial business card</title>
<link rel="stylesheet" href="https://fonts.googleapis.com/css2?family=Open+Sans:wght@400;700;800&display=swap">
<style>
  :root {
    --orange: #f07d22;
    --ink: #202024;
    --blue: #3a73b8;
    --white: #ffffff;
    --stage: #d9d9d9;
    --tag-grey: #2b2b2b;
  }
  * { box-sizing: border-box; margin: 0; padding: 0; }
  html, body {
    width: 1200px; height: 936px; overflow: hidden;
    background: var(--stage);
    font-family: "Open Sans", Arial, sans-serif;
  }
  .spread {
    position: relative; width: 1200px; height: 936px;
    display: flex; align-items: center; justify-content: center; gap: 40px;
  }
  .card {
    position: relative; width: 540px; height: 309px; overflow: hidden;
    box-shadow: 0 6px 18px rgba(0,0,0,.18);
  }

  /* Contact side */
  .card--contact { background: var(--ink); }
  .contact__band {
    position: absolute; left: 0; top: 150px; width: 320px; height: 159px;
    background: var(--orange);
  }
  .contact__accent {
    position: absolute; right: 0; bottom: 0; width: 240px; height: 130px;
    background: var(--blue);
  }
  .brand { position: absolute; left: 26px; top: 22px; }
  .brand__name {
    font-weight: 800; font-size: 38px; line-height: 1; letter-spacing: -1px;
    color: var(--blue);
  }
  .brand__tagline {
    margin-top: 4px; font-size: 13px; color: var(--blue); letter-spacing: -.2px;
  }
  .person {
    position: absolute; right: 36px; top: 104px;
    font-weight: 700; font-size: 24px; letter-spacing: .5px;
  }
  .person__first { color: var(--orange); }
  .person__last { color: var(--blue); }
  .person__mark {
    position: absolute; right: 0; top: 110px; width: 18px; height: 22px;
    background: var(--orange);
  }
  .details {
    position: absolute; left: 24px; top: 168px; width: 290px; list-style: none;
    color: var(--white); font-size: 13px; line-height: 1.45;
  }
  .details li { display: flex; align-items: center; gap: 7px; }
  .details svg { width: 12px; height: 12px; flex: none; fill: var(--white); }
  .details .spacer { height: 4px; }

  /* Logo side */
  .card--logo {
    background: var(--orange);
    display: flex; flex-direction: column; align-items: center; justify-content: center;
  }
  .card--logo .brand__name {
    font-size: 62px; color: #111; letter-spacing: -2px;
  }
  .card--logo .brand__tagline {
    font-size: 19px; color: var(--tag-grey); margin-top: 2px;
  }
</style>
</head>
<body>
<main class="spread">

  <section class="card card--contact" aria-label="Card front with contact details">
    <div class="contact__band"></div>
    <div class="contact__accent" role="img" aria-label="Blue brand block"></div>

    <div class="brand">
      <div class="brand__name">VEXTORIAL</div>
      <div class="brand__tagline">developer of custom applications</div>
    </div>

    <div class="person"><span class="person__first">Dale</span> <span class="person__last">Parker</span></div>
    <div class="person__mark"></div>

    <ul class="details">
      <li class="services">Custom software &amp; Bitcoin services</li>
      <li class="services">Bitcoin education &amp; payment integration</li>
      <li class="spacer"></li>
      <li>
        <svg viewBox="0 0 24 24" aria-hidden="true"><path d="M6.6 10.8a15.1 15.1 0 0 0 6.6 6.6l2.2-2.2a1 1 0 0 1 1-.25 11.4 11.4 0 0 0 3.6.57 1 1 0 0 1 1 1V20a1 1 0 0 1-1 1A17 17 0 0 1 3 4a1 1 0 0 1 1-1h3.5a1 1 0 0 1 1 1c0 1.25.2 2.45.57 3.57a1 1 0 0 1-.25 1z"/></svg>
        (888) 555-VXTRL
      </li>
      <li>
        <svg viewBox="0 0 24 24" aria-hidden="true"><circle cx="12" cy="12" r="10" fill="none" stroke="#fff" stroke-width="2.4"/><path d="M2 12h20M12 2c3 3 3 17 0 20M12 2c-3 3-3 17 0 20" fill="none" stroke="#fff" stroke-width="2"/></svg>
        www.vextorial.com
      </li>
      <li>
        <svg viewBox="0 0 24 24" aria-hidden="true"><path d="M2 5h20v14H2z" fill="none" stroke="#fff" stroke-width="2.4"/><path d="M2 5l10 8 10-8" fill="none" stroke="#fff" stroke-width="2.4"/></svg>
        dale@vextorial.com
      </li>
    </ul>
  </section>

  <section class="card card--logo" aria-label="Card back with company name">
    <div class="brand__name">VEXTORIAL</div>
    <div class="brand__tagline">developer of custom applications</div>
  </section>

</main>
</body>
</html>
```